Business Card Design for Training Business

Clear Path Coaching is a new business that delivers training and other services with a focus on topics related to mental health and wellbeing, for example, Wellmind Response Course, Resilience etc. We have a strong focus on evidence-based psychology and neuroscience. I have a logo which I will upload with the brief, so please consider colours that work well with the logo.
Target Market(s)
Adults, workplaces (particularly government and not-for-profits)
Industry/Entity Type
Business
Contact Information for Business Card
Head Strong TrainingSamantha SellwoodDirector0438 770 850sam@headstrongtraining.com.auwww.headstrongtraining.com.au

```html
<!DOCTYPE html>
<html lang="en">
<head>
<meta charset="utf-8">
<title>Clear Path Coaching – Business Card</title>
<link href="https://fonts.googleapis.com/css2?family=Arimo:wght@400;700&display=swap" rel="stylesheet">
<style>
  :root {
    --page-bg: #e9e7e4;
    --card-white: #ffffff;
    --card-white-shade: #e6e6e6;
    --card-grey-light: #8a8a8b;
    --card-grey-dark: #6b6b6c;
    --accent-teal: #2aa9ad;
    --ink: #161616;
    --logo-ink: #4a4a4a;
  }
  * { margin: 0; padding: 0; box-sizing: border-box; }
  html, body {
    width: 1200px; height: 892px; overflow: hidden;
    background: var(--page-bg);
    font-family: "Arimo", Arial, sans-serif;
  }
  .card {
    position: absolute; left: 120px; top: 172px;
    width: 960px; height: 548px;
    border-radius: 44px; overflow: hidden;
    background: linear-gradient(180deg, var(--card-white) 0%, var(--card-white-shade) 100%);
    box-shadow: 0 18px 40px rgba(0,0,0,0.25);
  }
  .card-shapes { position: absolute; inset: 0; }
  .brand {
    position: absolute; left: 130px; top: 60px;
    display: flex; align-items: center; gap: 28px;
    color: var(--logo-ink); font-weight: 400;
  }
  .brand-mark {
    width: 120px; height: 120px; border-radius: 50%;
    border: 3px solid var(--accent-teal);
  }
  .brand-name { line-height: 1; }
  .brand-name .line-main { display: block; font-size: 48px; letter-spacing: 5px; }
  .brand-name .line-sub { display: block; font-size: 20px; letter-spacing: 14px; margin-top: 12px; text-align: right; }
  .person {
    position: absolute; right: 488px; top: 420px; text-align: right; color: var(--ink);
  }
  .person-name { font-size: 32px; font-weight: 700; }
  .person-role { font-size: 21px; font-weight: 700; margin-top: 6px; }
  .divider {
    position: absolute; left: 500px; top: 318px; width: 2px; height: 178px;
    background: #3a3a3a;
  }
  .contacts {
    position: absolute; left: 530px; top: 334px; list-style: none; color: var(--ink);
    font-size: 21px;
  }
  .contacts li { display: flex; align-items: center; gap: 16px; height: 46px; white-space: nowrap; }
  .contacts svg { width: 20px; height: 20px; flex: none; }
</style>
</head>
<body>
  <div class="card">
    <svg class="card-shapes" viewBox="0 0 960 548" preserveAspectRatio="none" aria-hidden="true">
      <defs>
        <linearGradient id="greyBand" x1="0" y1="0" x2="0" y2="1">
          <stop offset="0" stop-color="var(--card-grey-light)"/>
          <stop offset="1" stop-color="var(--card-grey-dark)"/>
        </linearGradient>
      </defs>
      <path d="M0 318 Q 640 330 960 48 L960 548 L0 548 Z" fill="url(#greyBand)"/>
      <path d="M0 318 Q 640 330 960 48 L960 30 Q 650 300 0 312 Z" fill="var(--card-white)"/>
      <path d="M40 312 Q 650 296 960 16 L960 30 Q 650 292 40 312 Z" fill="var(--accent-teal)"/>
      <path d="M40 312 Q 660 318 960 10 L960 18 Q 650 296 40 312 Z" fill="var(--accent-teal)"/>
    </svg>

    <div class="brand">
      <div class="brand-mark"></div>
      <div class="brand-name">
        <span class="line-main">CLEAR PATH</span>
        <span class="line-sub">COACHING</span>
      </div>
    </div>

    <div class="person">
      <div class="person-name">Rebecca Tanfield</div>
      <div class="person-role">Director</div>
    </div>

    <div class="divider"></div>

    <ul class="contacts">
      <li>
        <svg viewBox="0 0 20 20"><rect width="20" height="20" rx="2" fill="#1b1b1b"/><path d="M6 4.5l2 2-1.2 1.6c.8 1.7 2 2.9 3.6 3.7L12 10.6l2.1 2-1.3 2.4C8.5 14.5 5.4 11.4 4.5 6z" fill="#fff"/></svg>
        <span>0491 362 517</span>
      </li>
      <li>
        <svg viewBox="0 0 20 20"><rect width="20" height="20" rx="2" fill="#1b1b1b"/><rect x="4" y="6" width="12" height="8" fill="none" stroke="#fff" stroke-width="1.4"/><path d="M4 6l6 5 6-5" fill="none" stroke="#fff" stroke-width="1.4"/></svg>
        <span>bec@clearpathcoaching.example.au</span>
      </li>
      <li>
        <svg viewBox="0 0 20 20"><rect width="20" height="20" rx="2" fill="#1b1b1b"/><circle cx="10" cy="10" r="5.5" fill="none" stroke="#fff" stroke-width="1.3"/><path d="M4.5 10h11M10 4.5c-2.5 3-2.5 8 0 11M10 4.5c2.5 3 2.5 8 0 11" fill="none" stroke="#fff" stroke-width="1.1"/></svg>
        <span>www.clearpathcoaching.example.au</span>
      </li>
    </ul>
  </div>
</body>
</html>
```